Meadowlark Property Review is a leading provider of residential appraisal and home inspection products in S

I need a business card/logo designed that obviously describes my business. We are a residential appraisal and home inspection company in Springfield, MO. We offer residential appraisals, home inspection, pest inspection and radon gas measurement. We have been in business for 18 years and hold state certified residential appraisal licenses and OBREX certified home inspection licenses. I have a logo that I really like and will attach, but would be open to new suggestions. I like more modern designs than traditional and would like a two sided card with our services, licenses and qualifications on the back.

```html
<!DOCTYPE html>
<html lang="en">
<head>
<meta charset="utf-8">
<title>Meadowlark Property Review – Business Card</title>
<link href="https://fonts.googleapis.com/css2?family=Source+Sans+3:ital,wght@0,400;0,600;1,400&display=swap" rel="stylesheet">
<style>
  :root {
    --backdrop: #3b3b3b;
    --card-white: #f7f7f7;
    --brand-brown: #8b6a42;
    --brand-orange: #f08a1c;
    --ink-white: #ffffff;
    --ink-soft: #efe4d6;
  }
  * { box-sizing: border-box; margin: 0; padding: 0; }
  html, body {
    width: 1200px; height: 750px; overflow: hidden;
    background: var(--backdrop);
    font-family: "Source Sans 3", "Myriad Pro", sans-serif;
  }
  .canvas { position: relative; width: 1200px; height: 750px; }
  .card {
    position: absolute; top: 228px;
    width: 461px; height: 263px; overflow: hidden;
  }
  .card--front { left: 124px; background: var(--card-white); }
  .card--back { left: 619px; background: var(--brand-brown); }

  .front-diagonal { position: absolute; inset: 0; }

  .company-name {
    position: absolute; left: 42px; top: 76px;
    display: flex; align-items: center; gap: 8px;
    color: var(--brand-brown); font-weight: 600; font-size: 18px; line-height: 1;
  }
  .company-name .mark-square {
    width: 11px; height: 11px; background: var(--brand-orange);
  }

  .person { position: absolute; left: 43px; top: 139px; }
  .person-name { color: var(--brand-brown); font-weight: 600; font-size: 17px; line-height: 1.2; }
  .person-title { color: var(--brand-orange); font-size: 13px; line-height: 1.3; }

  .contact {
    position: absolute; right: 27px; top: 138px;
    color: var(--ink-white); font-size: 11.5px; text-align: right; line-height: 14.5px;
  }
  .contact-address { margin-bottom: 6px; }
  .contact-line {
    display: flex; justify-content: flex-end; align-items: center; gap: 7px;
    height: 17.5px;
  }
  .contact-line svg { width: 12px; height: 12px; flex: none; }

  .back-name {
    position: absolute; left: 0; right: 0; top: 92px;
    text-align: center; color: var(--ink-white);
    font-weight: 600; font-size: 24px; line-height: 1;
  }
  .services {
    position: absolute; left: 0; right: 0; top: 160px;
    text-align: center; color: var(--ink-white);
    font-style: italic; font-size: 12.5px; line-height: 18px;
  }
  .services .bullet,
  .credentials .bullet { color: var(--brand-orange); font-style: normal; padding: 0 3px; }
  .credentials {
    position: absolute; left: 0; right: 0; top: 210px;
    text-align: center; color: var(--ink-soft);
    font-size: 11px; line-height: 16px;
  }
</style>
</head>
<body>
<main class="canvas">

  <section class="card card--front" aria-label="Business card front">
    <svg class="front-diagonal" viewBox="0 0 461 263" preserveAspectRatio="none" aria-hidden="true">
      <polygon points="141,263 461,7 461,263" fill="var(--brand-brown)"/>
      <line x1="131" y1="263" x2="461" y2="-1" stroke="var(--brand-orange)" stroke-width="3"/>
    </svg>

    <div class="company-name"><span class="mark-square"></span>Meadowlark Property Review</div>

    <div class="person">
      <p class="person-name">Daniel Reyes</p>
      <p class="person-title">CEO/Founder</p>
    </div>

    <div class="contact">
      <p class="contact-address">4120 Larkspur Court<br>Springfield, Missouri 65804</p>
      <p class="contact-line">417 555 0186
        <svg viewBox="0 0 24 24" aria-hidden="true"><path fill="#fff" d="M6.6 10.8a15.1 15.1 0 0 0 6.6 6.6l2.2-2.2c.3-.3.7-.4 1-.2 1.1.4 2.3.6 3.6.6.6 0 1 .4 1 1V20c0 .6-.4 1-1 1A17 17 0 0 1 3 4c0-.6.4-1 1-1h3.5c.6 0 1 .4 1 1 0 1.3.2 2.5.6 3.6.1.3 0 .7-.2 1z"/></svg>
      </p>
      <p class="contact-line">417 555 0142
        <svg viewBox="0 0 24 24" aria-hidden="true"><path fill="#fff" d="M6 2h12v5H6zM3 8h18a1 1 0 0 1 1 1v8h-4v-3H6v3H2V9a1 1 0 0 1 1-1zm4 7h10v7H7z"/></svg>
      </p>
      <p class="contact-line">hello@meadowlarkreview.com
        <svg viewBox="0 0 24 24" aria-hidden="true"><path fill="#fff" d="M2 5h20v14H2zm2 2v.5l8 5 8-5V7z"/></svg>
      </p>
      <p class="contact-line">www.meadowlarkreview.com
        <svg viewBox="0 0 24 24" aria-hidden="true"><circle cx="12" cy="12" r="10" fill="#fff"/><path fill="var(--brand-brown)" d="M9 6c2 0 3 1 2 3s-3 1-3 3 2 2 2 4-2 2-3 1-2-4-1-7 1-4 3-4zm7 5c1 0 2 1 2 2s-1 3-2 3-1-2-1-3 0-2 1-2z"/></svg>
      </p>
    </div>
  </section>

  <section class="card card--back" aria-label="Business card back">
    <p class="back-name">Meadowlark Property Review</p>
    <p class="services">
      Residential appraisals <span class="bullet">•</span> Home inspection<br>
      Pest inspection and radon gas measurement.
    </p>
    <p class="credentials">
      State certified residential appraiser <span class="bullet">•</span> OBREX certified home inspector<br>
      Serving Springfield for 18 years
    </p>
  </section>

</main>
</body>
</html>
```